Brookvane Consulting Business Card Design

Business Card Design for Brookvane Consulting. Brookvane Consulting is a boutique consultancy based in Atlanta, GA., that specializes in marketing strategy, organization planning, and leadership development. We provide solutions for small businesses and startups as well as Vantage 300 companies.

http://brookvaneconsulting.com/

Target Market(s)

We provide solutions for small businesses and startups as well as Vantage 300 companies.

Industry/Entity Type

Consulting

Contact Information for Business Card

Two sided business card with priority on contact information, logo, tag line (Inspiration to Dream More, Do More, Become More)

Colors

Designer to choose colors to be used in the design.

Requirements
Must have
• contact information, logo, tag line (Inspiration to Dream More, Do More, Become More)
• Simple no over communication.
Nice to have
• I would like to see different placements of logo and creative use of both sides of the card
Should not have
• Do not put too much information on the card.

```html
<!DOCTYPE html>
<html lang="en">
<head>
<meta charset="utf-8">
<title>Brookvane Consulting Business Card</title>
<link rel="stylesheet" href="https://fonts.googleapis.com/css2?family=Lato:wght@300;400&display=swap">
<style>
  :root {
    --stage-light: #8a8a8a;
    --stage-dark: #3a3a3a;
    --card-black: #0c0c0c;
    --card-sheen: #2a2a2a;
    --card-edge: #1b1b1b;
    --ink-white: #f4f4f4;
    --ink-soft: #cfcfcf;
    --ink-muted: #8d8d8d;
    --divider: #4a4a4a;
  }
  html, body {
    margin: 0;
    padding: 0;
    width: 1200px;
    height: 886px;
    overflow: hidden;
  }
  body {
    background: radial-gradient(ellipse at 50% 45%, var(--stage-light) 0%, #5a5a5a 45%, var(--stage-dark) 100%);
    font-family: "Lato", sans-serif;
    position: relative;
  }
  .card {
    position: absolute;
    left: 320px;
    width: 560px;
    height: 320px;
    background: radial-gradient(ellipse at 40% 30%, var(--card-sheen) 0%, var(--card-black) 65%);
    box-shadow: 0 18px 40px rgba(0,0,0,0.55);
    box-sizing: border-box;
    color: var(--ink-white);
  }
  .card-front { top: 60px; }
  .card-back {
    top: 470px;
    border: 10px solid var(--card-edge);
  }
  .brand {
    display: flex;
    align-items: center;
    gap: 12px;
    font-weight: 400;
    font-size: 34px;
    letter-spacing: 0.5px;
    color: var(--ink-white);
    white-space: nowrap;
  }
  .brand-mark {
    width: 14px;
    height: 14px;
    background: var(--ink-white);
  }
  .card-front .brand {
    position: absolute;
    top: 110px;
    left: 0;
    right: 0;
    justify-content: center;
  }
  .tagline {
    position: absolute;
    bottom: 62px;
    left: 0;
    right: 0;
    text-align: center;
    font-size: 14px;
    font-weight: 300;
    color: var(--ink-soft);
    letter-spacing: 0.4px;
  }
  .card-back .brand {
    position: absolute;
    left: 34px;
    top: 130px;
    font-size: 24px;
    gap: 9px;
  }
  .card-back .brand-mark { width: 10px; height: 10px; }
  .divider {
    position: absolute;
    left: 300px;
    top: 30px;
    bottom: 30px;
    width: 1px;
    background: linear-gradient(to bottom, transparent, var(--divider) 30%, var(--divider) 70%, transparent);
  }
  .contact {
    position: absolute;
    left: 322px;
    top: 78px;
    right: 10px;
  }
  .contact-name {
    margin: 0;
    font-size: 17px;
    font-weight: 400;
    letter-spacing: 1px;
    text-transform: uppercase;
    color: var(--ink-muted);
  }
  .contact-role {
    margin: 3px 0 22px;
    font-size: 13px;
    color: var(--ink-soft);
  }
  .contact-list {
    list-style: none;
    margin: 0;
    padding: 0;
    font-size: 11.5px;
    color: var(--ink-soft);
  }
  .contact-list li {
    display: flex;
    align-items: center;
    gap: 8px;
    margin-bottom: 7px;
  }
  .contact-list svg {
    width: 11px;
    height: 11px;
    fill: var(--ink-soft);
    flex: none;
  }
</style>
</head>
<body>
  <section class="card card-front" aria-label="Card front">
    <div class="brand"><span class="brand-mark"></span>Brookvane Consulting</div>
    <p class="tagline">Inspiration to Dream More, Do More, Become More</p>
  </section>

  <section class="card card-back" aria-label="Card back">
    <div class="brand"><span class="brand-mark"></span>Brookvane Consulting</div>
    <div class="divider"></div>
    <div class="contact">
      <h2 class="contact-name">Darius Whitfield</h2>
      <p class="contact-role">Founder/Managing Director</p>
      <ul class="contact-list">
        <li>
          <svg viewBox="0 0 24 24" aria-hidden="true"><path d="M6.6 10.8a15.1 15.1 0 0 0 6.6 6.6l2.2-2.2c.3-.3.7-.4 1-.2 1.1.4 2.3.6 3.6.6.6 0 1 .4 1 1V20c0 .6-.4 1-1 1A17 17 0 0 1 3 4c0-.6.4-1 1-1h3.5c.6 0 1 .4 1 1 0 1.3.2 2.5.6 3.6.1.3 0 .7-.2 1z"/></svg>
          404-555-0172
        </li>
        <li>
          <svg viewBox="0 0 24 24" aria-hidden="true"><path d="M2 5h20v14H2zM4 7v.4l8 5.2 8-5.2V7zm0 2.8V17h16V9.8l-8 5.2z"/></svg>
          darius@brookvaneconsulting.com
        </li>
        <li>
          <svg viewBox="0 0 24 24" aria-hidden="true"><circle cx="12" cy="12" r="10"/></svg>
          brookvaneconsulting.com
        </li>
      </ul>
    </div>
  </section>
</body>
</html>
```